Dorvik Electric Ltd

Looking for a single page website and Facebook page design. I am an electrical contractor based on Vancouver Island. I do service, custom homes, residential and commercial installations. My company just started out, so I don't have any pictures of installs yet. I have 25 years experience. I would like the colors to be my logo colors black and I have a black Brandt Halvard that will be my vehicle which I will have a wrap for.
Updates

I just posted the contest today, not sure why the deadline is the same day.

Industry/Entity Type

Electrician

Requirements
Must have
• Services provided, About me section, quote section,
Nice to have
• I am not quite sure yet, I need to see some designs first .

```html
<!DOCTYPE html>
<html lang="en">
<head>
<meta charset="utf-8">
<title>Dorvik Electric Ltd</title>
<link href="https://fonts.googleapis.com/css2?family=Montserrat:wght@500;600;700&family=Arimo:wght@400;700&family=Great+Vibes&display=swap" rel="stylesheet">
<style>
:root{
  --yellow:#f5b301;
  --yellow-deep:#e09e00;
  --black:#000;
  --panel:#0e0e0e;
  --panel-2:#151515;
  --white:#fff;
  --muted:#6f6f6f;
  --text:#e6e6e6;
}
*{margin:0;padding:0;box-sizing:border-box}
html,body{width:1200px;height:4474px;overflow:hidden;background:var(--black)}
body{position:relative;font-family:"Arimo",Arial,sans-serif;color:var(--text)}
.abs{position:absolute}
.heading{font-family:"Montserrat",Arial,sans-serif;font-weight:600;color:var(--white);text-transform:uppercase}
.rule{position:absolute;height:3px;width:30px;background:var(--yellow)}
.btn{position:absolute;height:38px;padding:0 20px;background:var(--yellow);color:#111;font-family:"Montserrat",Arial,sans-serif;font-weight:700;font-size:12px;text-transform:uppercase;display:flex;align-items:center;gap:8px}
.btn .dot{width:11px;height:11px;border-radius:50%;background:#111;display:inline-block;position:relative}
.btn .dot::after{content:"";position:absolute;left:3px;top:3px;width:3px;height:3px;border-top:1.6px solid var(--yellow);border-right:1.6px solid var(--yellow);transform:rotate(45deg)}
.btn.framed{box-shadow:-6px 6px 0 -2px var(--black),-8px 8px 0 -2px var(--yellow)}
.btn.outline{background:#000;color:var(--yellow);border-left:3px solid var(--yellow);border-top:3px solid var(--yellow)}
.btn.outline .dot{background:var(--yellow)}
.btn.outline .dot::after{border-color:#000}
.body-text{font-size:14px;line-height:25.6px;color:var(--text);text-align:justify}

/* header */
.top-line{left:0;top:0;width:1200px;height:5px;background:var(--yellow)}
.brand{display:flex;align-items:center;gap:10px;font-family:"Montserrat",Arial,sans-serif;font-weight:700;font-size:16px;color:var(--white);letter-spacing:.3px}
.brand .mark{width:46px;height:46px;border-radius:50%;border:3px solid var(--yellow)}
.nav{left:482px;top:93px;font-family:"Montserrat",Arial,sans-serif;font-weight:600;font-size:13px;color:var(--white)}
.nav a{color:inherit;text-decoration:none;position:absolute;white-space:nowrap}
.nav a.active{color:var(--yellow)}
.social{width:26px;height:26px;border-radius:50%;background:var(--yellow)}
.call-label{font-family:"Montserrat",Arial,sans-serif;font-weight:700;font-size:10px;color:var(--white)}
.call-num{font-family:"Montserrat",Arial,sans-serif;font-weight:700;font-size:16px;color:var(--white)}

/* services */
.service-title{font-family:"Montserrat",Arial,sans-serif;font-weight:700;font-size:16px;text-align:center;color:var(--white)}
.service-text{font-size:12.5px;line-height:19.5px;color:var(--muted);text-align:center}
.more{font-family:"Montserrat",Arial,sans-serif;font-weight:700;font-size:12px;color:var(--white);text-decoration:underline;display:flex;align-items:center;gap:6px;justify-content:center}
.more .dot{width:11px;height:11px;border-radius:50%;background:var(--white);position:relative}
.more .dot::after{content:"";position:absolute;left:3px;top:3px;width:3px;height:3px;border-top:1.6px solid #000;border-right:1.6px solid #000;transform:rotate(45deg)}
.more.gold{color:var(--yellow)}
.more.gold .dot{background:var(--yellow)}

/* works */
.work{position:absolute}

/* footer */
.foot-head{font-family:"Montserrat",Arial,sans-serif;font-weight:700;font-size:15px;color:var(--white);text-decoration:underline}
.foot-list{list-style:none;font-size:13.5px;color:var(--white)}
.foot-list li{height:34.4px;display:flex;align-items:center;gap:12px}
.foot-list li::before{content:"»";color:var(--yellow);font-size:14px}
.contact-item{display:flex;align-items:center;gap:14px;font-size:13.5px;color:var(--white)}
.contact-item .ring{width:40px;height:40px;border-radius:50%;border:1px solid #3a3a3a;display:flex;align-items:center;justify-content:center}
.contact-item b{font-weight:700}
.social-sm{width:32px;height:32px;border-radius:50%;border:1px solid #444;display:flex;align-items:center;justify-content:center}
.social-sm::after{content:"";width:10px;height:10px;border-radius:50%;background:var(--yellow)}
</style>
</head>
<body>

<!-- Header -->
<header>
  <div class="abs top-line"></div>
  <div class="abs brand" style="left:122px;top:40px"><span class="mark"></span>DORVIK ELECTRIC Ltd</div>
  <div class="abs social" style="left:756px;top:34px"></div>
  <div class="abs social" style="left:796px;top:34px"></div>
  <div class="abs social" style="left:834px;top:34px"></div>
  <svg class="abs" style="left:898px;top:26px" width="44" height="44" viewBox="0 0 44 44" aria-hidden="true">
    <circle cx="22" cy="22" r="19" fill="none" stroke="var(--yellow)" stroke-width="2.5"/>
    <path d="M15 13c2-1 4 3 3 5l-1 1c1 3 3 5 6 6l1-1c2-1 6 1 5 3l-2 3c-8 0-15-7-15-15z" fill="var(--yellow)"/>
  </svg>
  <div class="abs call-label" style="left:955px;top:29px">CALL US TODAY !</div>
  <div class="abs call-num" style="left:955px;top:47px">250-555-0143</div>
  <nav class="abs nav">
    <a class="active" style="left:0">Home</a>
    <a style="left:72px">Our Services</a>
    <a style="left:189px">About Us</a>
    <a style="left:282px">Quality &amp; Performance</a>
    <a style="left:462px">Our Work</a>
    <a style="left:553px">Contact</a>
  </nav>
</header>

<!-- Hero -->
<section>
  <div class="abs" role="img" aria-label="Evening city skyline over the harbour" style="left:0;top:132px;width:1200px;height:640px;background:
    radial-gradient(ellipse 70% 30% at 50% 62%,rgba(150,130,95,.45),transparent 70%),
    radial-gradient(ellipse 40% 22% at 18% 55%,rgba(120,110,90,.35),transparent 70%),
    radial-gradient(ellipse 40% 22% at 82% 58%,rgba(110,115,120,.35),transparent 70%),
    linear-gradient(180deg,#3b4452 0%,#4a525c 22%,#3a3f45 45%,#2a2c2e 68%,#101010 88%,#000 100%)"></div>
  <div class="abs" role="img" aria-label="Black Brandt Halvard pickup truck wrapped with Dorvik Electric branding" style="left:240px;top:470px;width:720px;height:280px;background:
    radial-gradient(ellipse 50% 45% at 50% 52%,rgba(8,8,8,.95) 0%,rgba(20,20,20,.85) 45%,rgba(30,30,30,.35) 75%,transparent 100%)"></div>
  <svg class="abs" style="left:0;top:132px" width="1200" height="660" viewBox="0 0 1200 660" aria-hidden="true">
    <polygon points="0,395 420,640 0,640" fill="#000"/>
    <polygon points="0,372 0,420 330,600 390,625" fill="var(--yellow)"/>
    <polygon points="1200,370 1200,640 640,640" fill="#000"/>
    <polygon points="1200,362 1200,410 900,465" fill="var(--yellow)"/>
  </svg>
  <div class="abs heading" style="left:0;top:205px;width:1200px;text-align:center;font-size:25px">Welcome to</div>
  <div class="abs heading" style="left:0;top:252px;width:1200px;text-align:center;font-size:42px;font-weight:700">Dorvik <span style="color:var(--yellow)">Electric</span> Ltd</div>
  <p class="abs" style="left:110px;top:328px;width:980px;text-align:center;font-size:14.5px;line-height:25px;color:var(--white)">Lorem ipsum dolor sit amet, consectetur adipiscing elit, sed do eiusmod tempor incididunt ut labore et dolore magna aliqua. Ut enim ad minim veniam, quis nostrud exercitation ullamco laboris nisi ut aliquip ex ea commodo consequat</p>
  <div class="btn framed" style="left:446px;top:405px">Get Started <span class="dot"></span></div>
  <div class="btn outline" style="left:610px;top:405px;height:40px">Service Inquiry <span class="dot"></span></div>
  <div class="abs" style="left:322px;top:722px;width:46px;height:46px;border-radius:50%;background:var(--white)"></div>
  <svg class="abs" style="left:332px;top:732px" width="26" height="26" viewBox="0 0 26 26" aria-hidden="true"><path d="M13 5v15M7 14l6 6 6-6" fill="none" stroke="#000" stroke-width="2.5"/></svg>
</section>

<!-- Services -->
<section>
  <div class="abs heading" style="left:0;top:784px;width:1200px;text-align:center;font-size:25px">Our Services</div>
  <div class="rule" style="left:585px;top:828px"></div>
  <svg class="abs" style="left:0;top:880px" width="1200" height="260" viewBox="0 0 1200 260" aria-hidden="true">
    <path d="M252 232 Q330 90 524 72" fill="none" stroke="var(--yellow)" stroke-width="2" stroke-dasharray="3 4"/>
    <path d="M948 232 Q870 90 676 72" fill="none" stroke="var(--yellow)" stroke-width="2" stroke-dasharray="3 4"/>
    <path d="M386 110 l12 -6 -6 12" fill="none" stroke="var(--yellow)" stroke-width="1.5"/>
    <path d="M808 110 l-12 -6 6 12" fill="none" stroke="var(--yellow)" stroke-width="1.5"/>
  </svg>
  <svg class="abs" style="left:521px;top:868px" width="156" height="140" viewBox="0 0 156 140" aria-hidden="true">
    <polygon points="39,0 117,0 156,70 117,140 39,140 0,70" fill="var(--yellow)"/>
    <rect x="54" y="40" width="30" height="60" fill="#000"/><rect x="84" y="58" width="20" height="42" fill="#000"/>
    <g fill="var(--yellow)"><rect x="59" y="47" width="5" height="5"/><rect x="69" y="47" width="5" height="5"/><rect x="59" y="58" width="5" height="5"/><rect x="69" y="58" width="5" height="5"/><rect x="59" y="69" width="5" height="5"/><rect x="69" y="69" width="5" height="5"/><rect x="59" y="80" width="5" height="5"/><rect x="69" y="80" width="5" height="5"/><rect x="89" y="66" width="4" height="4"/><rect x="96" y="66" width="4" height="4"/><rect x="89" y="76" width="4" height="4"/><rect x="96" y="76" width="4" height="4"/></g>
  </svg>
  <div class="abs service-title" style="left:400px;top:1018px;width:400px;color:var(--yellow)">Residential Installations</div>
  <p class="abs service-text" style="left:420px;top:1060px;width:360px;color:#555">Lorem ipsum dolor sit amet, consectadipiscing elit, sed do eiusmod tempor incididunt ut labore et dolore magna aliqua. Ut enim ad minim veniam, quis nostrud exercitation</p>
  <div class="abs more gold" style="left:500px;top:1130px;width:200px">LEARN MORE <span class="dot"></span></div>

  <svg class="abs" style="left:178px;top:1116px" width="140" height="150" viewBox="0 0 140 150" aria-hidden="true">
    <polygon points="70,2 138,38 138,112 70,148 2,112 2,38" fill="none" stroke="var(--yellow)" stroke-width="2"/>
    <path d="M70 45 L32 78 H42 V108 H62 V90 H78 V108 H98 V78 H108 Z" fill="var(--yellow)"/>
  </svg>
  <div class="abs service-title" style="left:98px;top:1288px;width:300px">Custom Homes</div>
  <div class="rule" style="left:233px;top:1322px;height:2px"></div>
  <p class="abs service-text" style="left:108px;top:1342px;width:280px">Lorem ipsum dolor sit amet, consectadipiscing elit, sed do eiusmod tempor incididunt ut labore et dolore magna aliqua.</p>
  <div class="abs more" style="left:148px;top:1424px;width:200px">LEARN MORE <span class="dot"></span></div>

  <svg class="abs" style="left:880px;top:1116px" width="140" height="150" viewBox="0 0 140 150" aria-hidden="true">
    <polygon points="70,2 138,38 138,112 70,148 2,112 2,38" fill="none" stroke="var(--yellow)" stroke-width="2"/>
    <path d="M45 48 L100 103" stroke="var(--yellow)" stroke-width="9" stroke-linecap="round"/>
    <path d="M100 48 L45 103" stroke="var(--yellow)" stroke-width="9" stroke-linecap="round"/>
    <circle cx="100" cy="48" r="10" fill="none" stroke="var(--yellow)" stroke-width="5"/>
  </svg>
  <div class="abs service-title" style="left:800px;top:1288px;width:300px">Commercial Installations</div>
  <div class="rule" style="left:935px;top:1322px;height:2px"></div>
  <p class="abs service-text" style="left:810px;top:1342px;width:280px">Lorem ipsum dolor sit amet, consectadipiscing elit, sed do eiusmod tempor incididunt ut labore et dolore magna aliqua.</p>
  <div class="abs more" style="left:850px;top:1424px;width:200px">LEARN MORE <span class="dot"></span></div>

  <div class="abs" style="left:448px;top:1206px;width:300px;height:244px;border-radius:50%;border:6px solid var(--yellow);display:flex;align-items:center;justify-content:center;font-family:'Montserrat',Arial,sans-serif;font-weight:700;font-size:26px;color:var(--white);text-align:center;line-height:34px">DORVIK<br>ELECTRIC</div>
</section>

<!-- About -->
<section>
  <svg class="abs" style="left:0;top:1490px" width="1200" height="670" viewBox="0 0 1200 670" aria-hidden="true">
    <polygon points="0,180 860,0 1200,200 1200,670 0,670" fill="var(--panel)"/>
    <polygon points="0,200 670,60 0,240" fill="var(--yellow)"/>
    <polygon points="900,50 1200,230 1200,250" fill="var(--yellow)"/>
  </svg>
  <div class="abs" role="img" aria-label="Electricians in hard hats and safety vests on a job site, framed in an oval" style="left:113px;top:1693px;width:425px;height:347px;border-radius:50%;border:5px solid #9aa8b3;background:
    radial-gradient(ellipse 22% 16% at 52% 52%,rgba(230,110,40,.75),transparent 75%),
    radial-gradient(ellipse 16% 12% at 48% 36%,rgba(240,200,60,.6),transparent 75%),
    radial-gradient(ellipse 60% 50% at 50% 50%,#8fa0ad,transparent 80%),
    linear-gradient(135deg,#dfe7ec 0%,#9fb0bd 35%,#5f7080 65%,#1e262c 100%)"></div>
  <div class="abs heading" style="left:660px;top:1705px;font-size:25px">About Us</div>
  <div class="rule" style="left:660px;top:1748px"></div>
  <p class="abs body-text" style="left:660px;top:1772px;width:429px">Sed ut perspiciatis unde omnis iste natus error sit voluptatem accusantium doloremque laudantium, totam rem aperiam, eaque ipsa quae ab illo inventore veritatis et quasi architecto beatae vitae dicta sunt explicabo. Nemo enim ipsam voluptatem quia voluptas sit aspernatur aut odit aut fugit, sed quia consequuntur magni dolores eos qui ratione voluptatem sequi nesciunt. Neque porro quisquam est, qui dolorem ipsum quia dolor sit amet, consectetur, adipisci velit, sed quia non numquam</p>
  <div class="btn" style="left:666px;top:2002px;box-shadow:0 0 0 3px #2a2a2a">Learn More <span class="dot"></span></div>
  <svg class="abs" style="left:352px;top:2120px" width="500" height="52" viewBox="0 0 500 52" aria-hidden="true">
    <path d="M4 4 L26 26 L4 48 H494" fill="none" stroke="var(--yellow)" stroke-width="1.5"/>
    <path d="M496 4 L474 26" fill="none" stroke="var(--yellow)" stroke-width="1.5"/>
  </svg>
  <div class="abs" style="left:352px;top:2124px;width:500px;text-align:center;font-family:'Great Vibes',cursive;font-size:25px;color:var(--yellow)">Serving Vancouver Island For Over <span style="font-size:36px">25</span> Years !</div>
</section>

<!-- Quality -->
<section>
  <div class="abs heading" style="left:111px;top:2280px;font-size:25px">Quality &amp; Performance</div>
  <div class="rule" style="left:111px;top:2322px"></div>
  <p class="abs body-text" style="left:111px;top:2347px;width:429px">Sed ut perspiciatis unde omnis iste natus error sit voluptatem accusantium doloremque laudantium, totam rem aperiam, eaque ipsa quae ab illo inventore veritatis et quasi architecto beatae vitae dicta sunt explicabo. Nemo enim ipsam voluptatem quia voluptas sit aspernatur aut odit aut fugit, sed quia consequuntur magni dolores eos qui ratione voluptatem sequi nesciunt. Neque porro quisquam est, qui dolorem ipsum quia dolor sit amet, consectetur, adipisci velit, sed quia non numquam</p>
  <div class="btn framed" style="left:120px;top:2580px">Learn More <span class="dot"></span></div>
  <div class="abs" style="left:622px;top:2284px;width:465px;height:342px;border-radius:50%;background:var(--white);box-shadow:12px 6px 0 0 var(--yellow)"></div>
  <div class="abs" role="img" aria-label="Two electricians in hard hats installing panels on a rooftop at dusk" style="left:638px;top:2296px;width:440px;height:318px;border-radius:50%;background:
    radial-gradient(ellipse 10% 22% at 44% 48%,rgba(225,120,40,.8),transparent 75%),
    radial-gradient(ellipse 12% 16% at 67% 62%,rgba(230,160,50,.7),transparent 75%),
    radial-gradient(ellipse 60% 30% at 50% 18%,#c9b9a3,transparent 75%),
    linear-gradient(180deg,#7e8893 0%,#a9aaa7 30%,#7f8489 55%,#4f5459 80%,#36393c 100%)"></div>
</section>

<!-- Service area -->
<section>
  <svg class="abs" style="left:0;top:2640px" width="1200" height="545" viewBox="0 0 1200 545" aria-hidden="true">
    <polygon points="0,0 300,250 1200,30 1200,545 0,545" fill="var(--panel-2)"/>
    <polygon points="0,0 300,250 0,40" fill="var(--yellow)"/>
    <polygon points="340,240 1200,10 1200,40" fill="var(--yellow)"/>
  </svg>
  <div class="abs heading" style="left:0;top:2918px;width:1200px;text-align:center;font-size:25px">Servicing All Areas of Vancouver Island</div>
  <p class="abs" style="left:111px;top:2993px;width:978px;text-align:center;font-size:14.5px;line-height:26px;color:var(--text)">Sed ut perspiciatis unde omnis iste natus error sit voluptatem accusantium doloremque laudantium, totam rem aperiam, eaque ipsa quae ab illo inventore veritatis et quasi architecto beatae vitae dicta sunt explicabo. Nemo enim ipsam voluptatem quia voluptas sit aspernatur aut odit aut fugit, sed quia consequuntur magni dolores</p>
  <div class="btn framed" style="left:530px;top:3096px">Service Inquiry <span class="dot"></span></div>
</section>

<!-- Works -->
<section>
  <div class="abs heading" style="left:0;top:3260px;width:1200px;text-align:center;font-size:25px">Our Works</div>
  <div class="rule" style="left:585px;top:3308px"></div>
  <div class="work" role="img" aria-label="Electrician kneeling beside a toolbox" style="left:111px;top:3346px;width:238px;height:466px;background:
    radial-gradient(ellipse 30% 8% at 62% 12%,rgba(240,190,30,.85),transparent 75%),
    radial-gradient(ellipse 45% 25% at 55% 45%,#7a3e38,transparent 75%),
    radial-gradient(ellipse 50% 18% at 45% 82%,#3c4247,transparent 80%),
    linear-gradient(160deg,#e4e4e1 0%,#bdbcb8 35%,#74706b 65%,#3a3a3a 100%)"></div>
  <div class="work" role="img" aria-label="Electrician in a high-visibility vest working overhead" style="left:358px;top:3346px;width:238px;height:229px;background:
    radial-gradient(ellipse 25% 20% at 55% 45%,rgba(190,220,70,.75),transparent 75%),
    linear-gradient(160deg,#d4d9dc 0%,#9aa6aa 40%,#4e5c56 75%,#2c3430 100%)"></div>
  <div class="work" role="img" aria-label="Electrician in a hard hat testing a switchboard" style="left:605px;top:3346px;width:484px;height:229px;background:
    radial-gradient(ellipse 9% 14% at 42% 12%,rgba(245,200,30,.9),transparent 75%),
    radial-gradient(ellipse 14% 30% at 42% 62%,rgba(200,215,60,.75),transparent 75%),
    linear-gradient(90deg,#4e5a60 0%,#7c8a90 25%,#a9b1ad 50%,#7e8c91 75%,#5a676c 100%)"></div>
  <div class="work" role="img" aria-label="Electrician installing a wall fixture" style="left:358px;top:3583px;width:238px;height:229px;background:
    radial-gradient(ellipse 22% 30% at 45% 70%,#2f4f8a,transparent 75%),
    linear-gradient(160deg,#f1f1ef 0%,#cfd0cf 45%,#8c929a 75%,#4a5568 100%)"></div>
  <div class="work" role="img" aria-label="Technician servicing a kitchen appliance" style="left:605px;top:3583px;width:238px;height:229px;background:
    radial-gradient(ellipse 20% 22% at 62% 62%,#3d5d96,transparent 75%),
    linear-gradient(160deg,#f3f2ee 0%,#dcd8cf 45%,#a59e91 75%,#6f685d 100%)"></div>
  <div class="work" role="img" aria-label="Electrician fitting a warm ceiling light" style="left:851px;top:3583px;width:238px;height:229px;background:
    radial-gradient(ellipse 22% 20% at 35% 68%,rgba(255,210,120,.9),transparent 75%),
    linear-gradient(160deg,#8a5a42 0%,#5e3a2c 45%,#33211a 80%,#1c130f 100%)"></div>
</section>

<!-- Footer -->
<footer>
  <svg class="abs" style="left:0;top:3900px" width="1200" height="190" viewBox="0 0 1200 190" aria-hidden="true">
    <polygon points="0,190 0,160 670,0 1200,130 1200,190" fill="var(--panel)"/>
    <polygon points="0,160 670,0 0,190" fill="var(--yellow)"/>
    <polygon points="0,170 620,22 0,190" fill="var(--panel)"/>
    <polygon points="940,10 1200,130 1200,170" fill="var(--yellow)"/>
  </svg>
  <div class="abs" style="left:0;top:4088px;width:1200px;height:333px;background:var(--panel)"></div>
  <div class="abs contact-item" style="left:128px;top:4080px"><span class="ring"><svg width="16" height="12" viewBox="0 0 16 12"><rect x="1" y="1" width="14" height="10" fill="none" stroke="var(--yellow)" stroke-width="1.5"/><path d="M1 1l7 6 7-6" fill="none" stroke="var(--yellow)" stroke-width="1.5"/></svg></span>info@dorvikelectric.ca</div>
  <div class="abs contact-item" style="left:397px;top:4080px"><span class="ring"><svg width="14" height="16" viewBox="0 0 14 16"><rect x="1" y="3" width="12" height="12" rx="2" fill="var(--yellow)"/></svg></span><b>250-555-0143</b></div>
  <div class="abs contact-item" style="left:603px;top:4080px"><span class="ring"><svg width="16" height="16" viewBox="0 0 16 16"><path d="M3 2c1-1 3 2 2 4l-1 1c1 2 3 4 5 5l1-1c2-1 5 1 4 2l-2 2C7 15 1 9 3 2z" fill="var(--yellow)"/></svg></span><b>250-555-0143</b></div>
  <div class="abs contact-item" style="left:807px;top:4080px;line-height:22px"><span class="ring"><svg width="12" height="16" viewBox="0 0 12 16"><path d="M6 15C2 9 1 7 1 5a5 5 0 0110 0c0 2-1 4-5 10z" fill="var(--yellow)"/><circle cx="6" cy="5" r="2" fill="var(--panel)"/></svg></span><span style="font-size:13px">418 Harbour Lane<br>Vancouver Island</span></div>
  <div class="abs" style="left:111px;top:4150px;width:978px;height:1px;background:#2c2c2c"></div>

  <div class="abs foot-head" style="left:113px;top:4186px">About Us</div>
  <p class="abs" style="left:113px;top:4226px;width:345px;font-size:12.5px;line-height:22px;color:var(--white);text-align:justify">Lorem ipsum dolor sit amet, consectetur adipiscing elit, sed do eiusmod tempor incididunt ut labore et dolore magna aliqua. Ut enim ad minim veniam, quis nostrud exercitation ullamco laboris</p>
  <div class="abs" style="left:113px;top:4330px;display:flex;gap:10px"><span class="social-sm"></span><span class="social-sm"></span><span class="social-sm"></span></div>

  <div class="abs foot-head" style="left:504px;top:4186px">Quick Links</div>
  <ul class="abs foot-list" style="left:504px;top:4222px">
    <li>Home</li><li>About Us</li><li>Our Services</li><li>Our Works</li><li>Quality &amp; Performance</li>
  </ul>
  <div class="abs foot-head" style="left:708px;top:4186px">Other Links</div>
  <ul class="abs foot-list" style="left:708px;top:4222px">
    <li>FAQ</li><li>Connect</li><li>Terms Of Service</li><li>Privacy Policy</li><li>Contact Us</li>
  </ul>
  <div class="abs" style="left:888px;top:4210px;width:200px;height:168px;border-radius:50%;border:5px solid var(--yellow);display:flex;align-items:center;justify-content:center;font-family:'Montserrat',Arial,sans-serif;font-weight:700;font-size:18px;line-height:24px;color:var(--white);text-align:center">DORVIK<br>ELECTRIC</div>

  <div class="abs" style="left:0;top:4421px;width:1200px;height:53px;background:var(--yellow);display:flex;align-items:center;justify-content:center;font-size:14px;color:#111">© 2022 Dorvik Electric Ltd. All Rights Reserved</div>
</footer>

</body>
</html>
```